SUNRISE ON STONE 1K/5K WALK/RUN HEALTH EXPO

NEED A HEALTH FAIR FLYER EMPHASIZING THE WALK AS WELL AS ALL HEALTH FAIR. MY VISION IS TO HAVE SOMEONE RUNNING WITH VARIOUS HEALTH CONDITIONS INSIDE THE BRAIN . AS MANY HEALTH CONDITIONS AS POSSIBLE SUCH AS HEART DISEASE, DIABETES, MENTAL HEALTH, AND AS MANY THAT CAN FIT IN THE BRAIN. THE HAIR CAN ALSO HAVE THE COLORS THAT REPRESENT THE HEALTH CONDITION. Eg. Pink represents breast cancer; red represent heart disease, mental Health is green
Details: Redmarsh Alumnae Chapter 1k/5k Health Expo
Date: 3/25/2023
Time: 8am - 1:00 PM (8am Check in/ Walk Starts at 9:00
Location: Hollowbrook Park, Fernhollow TX
Theme: Sunrise On Stone (We are bringing awareness to all health issues that are affecting our community
We would like everyone to wear the color in which they would like to bring awareness to. Eg. Pink for Breast Cancer
Green for Mental Health.)
Agenda: 8am Checkin
9am walk starts
10am-12 Music, Food, Fun, Prizes and Health Experts from the community : Working on Special Guest: Bolt Pup to lead the walk: Trying to get the Larkfield Cheerleaders
12-1: Closing Ceremony and Breakdown

```html
<!DOCTYPE html>
<html lang="en">
<head>
<meta charset="utf-8">
<title>Redmarsh Alumnae 1K/5K Health Expo</title>
<link rel="stylesheet" href="https://fonts.googleapis.com/css2?family=Montserrat:wght@400;500;600;700;800;900&display=swap">
<style>
  :root {
    --bg: #ffffff;
    --paper: #ffffff;
    --crimson: #961d22;
    --crimson-deep: #8a1a1f;
    --umber: #3d2a22;
    --gold: #f2c36e;
    --pill: #e8b06a;
    --ink: #111111;
    --rule: #444444;
    --peach: #f2a27c;
    --heart: #e8232f;
    --teal: #2fb6b8;
    --green: #1f9b3a;
    --pink: #ef6ee0;
  }
  * { margin: 0; padding: 0; box-sizing: border-box; }
  html, body { width: 1200px; height: 2837px; overflow: hidden; background: var(--bg); }
  body { position: relative; font-family: "Montserrat", sans-serif; }

  .poster {
    position: absolute;
    left: 50px; top: 631px;
    width: 775px; height: 1110px;
    transform: scale(1.4194);
    transform-origin: 0 0;
    background: var(--paper);
    overflow: hidden;
    box-shadow: 0 10px 30px rgba(0,0,0,.25);
  }
  .poster > * { position: absolute; }
  .backdrop { left: 0; top: 0; width: 775px; height: 1110px; }

  .title {
    left: 0; width: 775px; text-align: center;
    color: #fff; font-weight: 800; line-height: 1; letter-spacing: -1px;
  }
  .title--first { top: 48px; font-size: 84px; }
  .title--second { top: 128px; font-size: 84px; }
  .subtitle {
    top: 212px; left: 0; width: 775px; text-align: center;
    color: var(--gold); font-weight: 400; font-size: 47px; line-height: 1;
  }
  .theme-pill {
    left: 232px; top: 278px; width: 311px; height: 44px;
    border-radius: 22px; background: var(--pill);
    color: var(--crimson-deep); font-weight: 800; font-size: 26px;
    display: flex; align-items: center; justify-content: center;
    white-space: nowrap;
  }

  .condition {
    font-weight: 800; font-size: 13.5px; letter-spacing: -0.3px; color: var(--ink);
    padding-bottom: 6px; border-bottom: 1.5px solid var(--rule);
    white-space: nowrap; line-height: 1.1;
  }
  .condition--heart { left: 45px; top: 352px; width: 127px; }
  .condition--diabetes { left: 45px; top: 402px; width: 127px; }
  .condition--mental { left: 598px; top: 352px; width: 132px; }
  .condition--breast { left: 598px; top: 402px; width: 132px; }

  .mascot-art { left: 262px; top: 345px; width: 240px; height: 305px; }
  .skyline-art { left: 0; top: 520px; width: 775px; height: 95px; }

  .event-date {
    left: 45px; top: 672px; width: 690px;
    font-weight: 800; font-size: 77px; line-height: 1; letter-spacing: -1.5px;
    color: var(--ink); white-space: nowrap;
  }
  .event-date .day { color: var(--crimson); }
  .event-date sup { font-size: 40px; vertical-align: 30px; margin-right: 18px; }
  .brain-zero {
    display: inline-block; width: 46px; height: 58px; border-radius: 50%;
    background: var(--ink); vertical-align: -2px; margin: 0 2px;
  }
  .event-hours {
    left: 45px; top: 752px; width: 685px;
    font-weight: 600; font-size: 33px; line-height: 1; color: var(--ink);
    padding-bottom: 8px; border-bottom: 2px solid var(--rule); white-space: nowrap;
  }

  .slot-time { color: var(--crimson); font-weight: 700; font-size: 27px; line-height: 1; white-space: nowrap; }
  .slot-label { font-weight: 500; font-size: 15px; color: var(--ink); margin-top: 10px; line-height: 1.25; }
  .slot--checkin { left: 45px; top: 815px; }
  .slot--checkin .slot-time { padding-left: 7px; }
  .slot--checkin .slot-label, .slot--walk .slot-label { white-space: nowrap; }
  .slot--walk { left: 162px; top: 815px; }
  .slot--walk .slot-time { padding-left: 25px; }
  .slot--expo { left: 321px; top: 815px; width: 407px; padding-bottom: 8px; border-bottom: 1.5px solid var(--rule); }
  .slot--expo .slot-label { font-size: 13.6px; margin-top: 8px; }
  .slot--closing { left: 321px; top: 912px; width: 407px; padding-bottom: 10px; border-bottom: 1.5px solid var(--rule); }
  .slot--closing .slot-label { margin-top: 8px; letter-spacing: .3px; white-space: nowrap; }

  .venue { left: 321px; top: 990px; width: 420px; }
  .venue-name { font-weight: 700; font-size: 21px; color: var(--ink); line-height: 1.1; white-space: nowrap; }
  .venue-address { font-weight: 500; font-size: 13.5px; margin: 4px 0 0 4px; color: var(--ink); white-space: nowrap; }
  .venue-web { font-weight: 600; font-size: 16px; letter-spacing: 6.2px; margin-top: 6px; color: var(--ink); white-space: nowrap; }
  .venue-web span { color: var(--crimson); }

  .chapter-mark { left: 45px; top: 950px; width: 240px; display: flex; align-items: center; gap: 12px; }
  .chapter-mark .mark-square { width: 26px; height: 26px; background: var(--crimson); flex: none; }
  .chapter-mark .mark-name { color: var(--crimson); font-weight: 700; font-size: 19px; line-height: 1.2; }
</style>
</head>
<body>
  <main class="poster">
    <svg class="backdrop" viewBox="0 0 775 1110" aria-hidden="true">
      <polygon points="0,130 388,470 775,130 775,160 388,500 0,160" fill="var(--umber)"/>
      <polygon points="0,0 775,0 775,130 388,470 0,130" fill="var(--crimson)"/>
      <polyline points="183,360 208,360 208,392 370,392" fill="none" stroke="var(--heart)" stroke-width="2"/>
      <polyline points="183,410 385,410" fill="none" stroke="var(--teal)" stroke-width="2"/>
      <polyline points="587,360 562,360 562,392 430,392" fill="none" stroke="var(--green)" stroke-width="2"/>
      <polyline points="587,410 410,410" fill="none" stroke="var(--pink)" stroke-width="2"/>
      <circle cx="183" cy="360" r="5" fill="var(--heart)"/>
      <circle cx="183" cy="410" r="5" fill="var(--teal)"/>
      <circle cx="587" cy="360" r="5" fill="var(--green)"/>
      <circle cx="587" cy="410" r="5" fill="var(--pink)"/>
    </svg>

    <div class="skyline-art" role="img" aria-label="Dark red city skyline silhouette band" style="background: var(--crimson-deep);"></div>
    <div class="mascot-art" role="img" aria-label="Cartoon brain character in a striped headband running across the skyline" style="background: radial-gradient(ellipse at 50% 45%, #f7b08a 0%, var(--peach) 60%, rgba(242,162,124,0) 72%);"></div>

    <h1 class="title title--first">REDMARSH</h1>
    <div class="title title--second">ALUMNAE</div>
    <div class="subtitle">1K/5K HEALTH EXPO</div>
    <div class="theme-pill">SUNRISE ON STONE</div>

    <div class="condition condition--heart">HEART DISEASE</div>
    <div class="condition condition--diabetes">DIABETES</div>
    <div class="condition condition--mental">MENTAL HEALTH</div>
    <div class="condition condition--breast">BREAST CANCER</div>

    <div class="event-date"><span class="day">25<sup>TH</sup></span>MARCH 2<span class="brain-zero" role="img" aria-label="Brain icon standing in for zero"></span>23</div>
    <div class="event-hours">(8AM CHECK IN/ WALK STARTS AT 9:00)</div>

    <div class="slot slot--checkin"><div class="slot-time">8AM</div><div class="slot-label">CHECK IN</div></div>
    <div class="slot slot--walk"><div class="slot-time">9AM</div><div class="slot-label">WALK STARTS</div></div>
    <div class="slot slot--expo"><div class="slot-time">10AM-12PM</div><div class="slot-label">Music, Food, Fun, Prizes and Health Experts from the community : Special Guest: Trying to get the Cheerleaders</div></div>
    <div class="slot slot--closing"><div class="slot-time">12AM-1PM</div><div class="slot-label">CLOSING CEREMONY AND BREAKDOWN</div></div>

    <div class="chapter-mark"><span class="mark-square"></span><span class="mark-name">Redmarsh Alumnae Chapter</span></div>

    <div class="venue">
      <div class="venue-name">Hollowbrook Park, Fernhollow TX</div>
      <div class="venue-address">48 Cedar Lantern Blvd. Fernhollow , TX 70412</div>
      <div class="venue-web">www.<span>redmarshalumnae</span>.org</div>
    </div>
  </main>
</body>
</html>
```